Firm Stationery Design

I need a design for stationery, including: Stationery First Page, Stationery Second Sheet, Envelope, Mailing Label for Flat Envelopes, and Business Cards

```html
<!DOCTYPE html>
<html lang="en">
<head>
<meta charset="utf-8">
<title>Marlowe Law LLC — Business Cards</title>
<link rel="stylesheet" href="https://fonts.googleapis.com/css2?family=Arimo:wght@400;700&display=swap">
<style>
  :root {
    --backdrop: #1f1f21;
    --card-white: #ffffff;
    --brand-orange: #ffa000;
    --brand-orange-deep: #e98a00;
    --ink: #1c1c1c;
    --text-grey: #4a4a4a;
    --rule-grey: #c9c9c9;
  }
  * { margin: 0; padding: 0; box-sizing: border-box; }
  html, body {
    width: 1200px; height: 874px; overflow: hidden;
    background: var(--backdrop);
    font-family: "Arimo", Arial, sans-serif;
  }
  .stage {
    width: 1200px; height: 874px;
    display: flex; flex-direction: column;
    align-items: center; justify-content: center; gap: 44px;
  }
  .card {
    position: relative;
    width: 620px; height: 354px;
    border-radius: 18px;
    overflow: hidden;
  }

  /* Back of card */
  .card--back {
    background: var(--brand-orange);
    display: flex; align-items: center; justify-content: center;
  }
  .back-wordmark {
    display: flex; flex-direction: column; align-items: center; gap: 18px;
    margin-top: -20px;
    color: var(--brand-orange-deep);
    font-weight: 700; font-size: 38px; letter-spacing: 2px;
    line-height: 1.1; text-align: center;
  }
  .back-wordmark .mark-square {
    width: 92px; height: 92px; background: var(--brand-orange-deep);
  }

  /* Front of card */
  .card--front { background: var(--card-white); }
  .front-bands { position: absolute; left: 0; top: 0; }
  .front-wordmark {
    position: absolute; left: 30px; top: 66px; width: 240px;
    display: flex; flex-direction: column; align-items: center; gap: 12px;
    color: var(--ink);
    font-weight: 700; font-size: 28px; letter-spacing: 1px;
    line-height: 1.1; text-align: center;
  }
  .front-wordmark .mark-square {
    width: 76px; height: 76px; background: var(--brand-orange);
  }
  .divider {
    position: absolute; left: 292px; top: 48px;
    width: 1.5px; height: 200px;
    background: linear-gradient(to bottom, transparent, var(--rule-grey) 20%, var(--rule-grey) 80%, transparent);
  }
  .details {
    position: absolute; left: 318px; top: 66px;
    color: var(--text-grey); font-size: 15px; line-height: 1.3;
  }
  .person-name {
    color: var(--ink); font-weight: 700; font-size: 25px; letter-spacing: 0.5px;
    line-height: 1.1;
  }
  .person-title { color: var(--brand-orange); font-size: 14px; margin-bottom: 14px; }
  .address { margin-bottom: 10px; }
  .contact-line { display: flex; align-items: center; gap: 8px; }
  .contact-line svg { width: 12px; height: 12px; flex: none; }
  .website {
    position: absolute; right: 26px; bottom: 13px;
    color: var(--card-white); font-size: 15px;
  }
</style>
</head>
<body>
<main class="stage">

  <section class="card card--back" aria-label="Business card back">
    <div class="back-wordmark">
      <span class="mark-square"></span>
      <span>MARLOWE<br>LAW LLC</span>
    </div>
  </section>

  <section class="card card--front" aria-label="Business card front">
    <svg class="front-bands" width="620" height="354" viewBox="0 0 620 354" aria-hidden="true">
      <path d="M0 268 H404 L416 286 H0 Z" fill="var(--brand-orange)"/>
      <path d="M0 292 H414 Q420 292 424 300 L428 308 Q431 312 438 312 H620 V354 H0 Z" fill="var(--ink)"/>
    </svg>

    <div class="front-wordmark">
      <span class="mark-square"></span>
      <span>MARLOWE<br>LAW LLC</span>
    </div>

    <div class="divider"></div>

    <div class="details">
      <div class="person-name">DANIEL PRICE</div>
      <div class="person-title">President</div>
      <div class="address">412 Birchwood Avenue<br>Fairview, Canada 21908</div>
      <div class="contact-line">
        <svg viewBox="0 0 12 12"><path d="M2.5 1 L4.5 1 L5.3 3.6 L4 4.6 Q5 7 7.4 8 L8.4 6.7 L11 7.5 L11 9.5 Q11 11 9.5 11 Q1 10 1 2.5 Q1 1 2.5 1 Z" fill="var(--brand-orange)"/></svg>
        <span>555-210-4471</span>
      </div>
      <div class="contact-line">
        <svg viewBox="0 0 12 12"><rect x="3" y="0.8" width="6" height="10.4" rx="1" fill="none" stroke="var(--brand-orange)" stroke-width="1.3"/><circle cx="6" cy="9.4" r="0.6" fill="var(--brand-orange)"/></svg>
        <span>555-318-9026</span>
      </div>
      <div class="contact-line">
        <svg viewBox="0 0 12 12"><rect x="0.5" y="2.5" width="11" height="7.5" fill="var(--brand-orange)"/><path d="M0.5 2.5 L6 7 L11.5 2.5" fill="none" stroke="#fff" stroke-width="1"/></svg>
        <span>info@marlowelaw.com</span>
      </div>
    </div>

    <div class="website">www.marlowelaw.com</div>
  </section>

</main>
</body>
</html>
```